Salon and Spa Distributor Business Card

Need a business card. We are are distributor in the salon and spa industry. We identify with natural beauty. Need a card with:
Company Name: Petal Quarry"
Title: "President & CEO"
Address
Company Phone number
email
website
Tag Line:" The Professional Salon Source"

Industry/Entity Type

Business

Contact Information for Business Card

Name: Dov Strommen
Title: "President & CEO"
Address: 31 Harlow Ln, Bexmoor, NJ 07813
Company Phone number: 800-463-5918
email: dovstrommen@petalquarry.example
website: www.petalquarry.example

Requirements
Should not have
• No black backgrounds

```html
<!DOCTYPE html>
<html lang="en">
<head>
<meta charset="utf-8">
<title>Petal Quarry – Business Card</title>
<link rel="stylesheet" href="https://fonts.googleapis.com/css2?family=Questrial&family=Source+Sans+3:wght@400;600;700&display=swap">
<style>
  :root {
    --stage: #d6d6d6;
    --paper: #ffffff;
    --green-light: #5fb647;
    --green-deep: #3f9a3c;
    --green-ink: #3b8e3a;
    --green-logo: #4fae46;
    --brown: #3d2e2f;
    --white: #ffffff;
  }
  * { margin: 0; padding: 0; box-sizing: border-box; }
  html, body { width: 1200px; height: 900px; overflow: hidden; }
  body { background: var(--stage); position: relative; font-family: "Source Sans 3", sans-serif; }

  .card {
    position: absolute;
    top: 306px;
    width: 440px;
    height: 271px;
    border-radius: 10px;
    overflow: hidden;
  }

  /* Front */
  .card--front { left: 149px; background: var(--paper); }
  .front__band {
    position: absolute; left: 0; right: 0; top: 113px; bottom: 0;
    background: linear-gradient(180deg, var(--green-light), var(--green-deep));
  }
  .front__art { position: absolute; right: 0; top: 0; width: 200px; height: 271px; }
  .wordmark {
    position: absolute;
    font-family: "Questrial", sans-serif;
    font-weight: 400;
    white-space: nowrap;
  }
  .card--front .wordmark { left: 23px; top: 36px; font-size: 35px; color: var(--green-ink); }

  .contact { position: absolute; left: 24px; top: 137px; color: var(--white); }
  .contact__name { font-size: 16px; font-weight: 600; letter-spacing: 0.3px; line-height: 20px; }
  .contact__title { font-size: 12px; line-height: 14px; margin-bottom: 8px; }
  .contact__list { list-style: none; font-size: 12.5px; line-height: 16px; }
  .contact__list li { display: flex; align-items: center; gap: 6px; }
  .contact__list svg { width: 8px; height: 8px; fill: var(--white); flex: none; }
  .contact__address { font-size: 12.5px; margin-top: 9px; }

  /* Back */
  .card--back { left: 608px; background: var(--brown); }
  .back__mark {
    position: absolute; left: 78px; top: 70px;
    width: 72px; height: 72px; border-radius: 50%;
    background: var(--green-logo);
  }
  .card--back .wordmark { left: 182px; top: 88px; font-size: 35px; color: var(--green-logo); }
  .tagline-band {
    position: absolute; left: 0; right: 0; bottom: 0; height: 57px;
    background: linear-gradient(180deg, var(--green-light), var(--green-deep));
    display: flex; align-items: center; justify-content: center;
    color: var(--white); font-size: 13.5px; font-weight: 700; letter-spacing: 0.2px;
  }
</style>
</head>
<body>

  <section class="card card--front">
    <div class="front__band"></div>
    <svg class="front__art" viewBox="0 0 200 271" role="img" aria-label="Flowing leaf and hair illustration in green tones">
      <defs>
        <linearGradient id="artGreen" x1="0" y1="0" x2="1" y2="1">
          <stop offset="0" stop-color="#6cc24f"/>
          <stop offset="1" stop-color="#2f8a3a"/>
        </linearGradient>
      </defs>
      <path d="M40 271 C60 200 30 150 90 110 C130 80 160 60 170 15 C185 20 200 30 200 40 L200 271 Z" fill="url(#artGreen)" opacity="0.85"/>
    </svg>
    <div class="wordmark">Petal Quarry</div>
    <div class="contact">
      <p class="contact__name">DOV STROMMEN</p>
      <p class="contact__title">President &amp; CEO</p>
      <ul class="contact__list">
        <li><svg viewBox="0 0 10 10"><path d="M2 0.5 L3.6 2.6 L2.7 3.7 C3.4 5.1 4.9 6.6 6.3 7.3 L7.4 6.4 L9.5 8 L8.4 9.5 C4.5 9.3 0.7 5.5 0.5 1.6 Z"/></svg>800-463-5918</li>
        <li><svg viewBox="0 0 10 10"><path d="M0 2 H10 V8.5 H0 Z M0.6 2.4 L5 5.6 L9.4 2.4" stroke="#5fb647" stroke-width="0.8"/></svg>dovstrommen@petalquarry.example</li>
        <li><svg viewBox="0 0 10 10"><circle cx="5" cy="5" r="4.8"/></svg>www.petalquarry.example</li>
      </ul>
      <p class="contact__address">31 Harlow Ln, Bexmoor, NJ 07813</p>
    </div>
  </section>

  <section class="card card--back">
    <div class="back__mark"></div>
    <div class="wordmark">Petal Quarry</div>
    <div class="tagline-band">THE PROFESSIONAL SALON SOURCE</div>
  </section>

</body>
</html>
```